NEW Modern Sleek Business Card for VR Language Startup

Our startup is using VR to lead the next wave of world language education. We need a two-sided business card that introduces the larger organization (Brightloom Language Inc) and our contact info on one side and shows the product, Glimwoorld, on the other side.

Side 1 (contact info)= Brightloom Logo and Contact info (name, title, phone, email)

Side 2 (product)= Glimworld logo, text, and website
Text= Culturally Immersive Language Learning Games
Website= www.glimworld-play.com

Target Market(s)

Education, Technology

Contact Information for Business Card

Contact info will be updated upon approval of the design. For now, put this as a placeholder.

Perry Dunmore
Founder & CEO
pdunmore@quillpost-mail.net
(555)-014-2286

Font styles to use
Other font styles liked:
• Gibson and Century Gothic are the brand fonts

Requirements
Nice to have
• I would love to see cohesion between the design and colors of the two logos. I have attached a few business card designs that I like, so you can get a feel for my preferred style.

```html
<!DOCTYPE html>
<html lang="en">
<head>
<meta charset="utf-8">
<title>Brightloom Language – Business Card</title>
<link rel="stylesheet" href="https://fonts.googleapis.com/css2?family=Questrial&family=Montserrat:wght@600;700&display=swap">
<style>
  :root {
    --page-bg: #d6d5d1;
    --card-bg: #1f1f1f;
    --ink-light: #f4f4f4;
    --accent-cyan: #35c3ea;
    --deco-grey: #8c8c8c;
    --band-cyan: #2fc6f0;
    --band-violet: #8a5fb0;
    --band-red: #ec3352;
    --band-orange: #f36b3f;
  }
  * { box-sizing: border-box; margin: 0; padding: 0; }
  html, body { width: 1200px; height: 801px; overflow: hidden; }
  body {
    background: var(--page-bg);
    font-family: "Questrial", "Century Gothic", sans-serif;
    position: relative;
  }
  .card {
    position: absolute;
    width: 540px;
    height: 309px;
    background: var(--card-bg);
    overflow: hidden;
    box-shadow: 0 14px 30px rgba(0,0,0,0.25);
  }
  .card--contact { left: 40px; top: 246px; }
  .card--product { left: 620px; top: 246px; }
  .card__band {
    position: absolute;
    left: 0; right: 0; bottom: 0;
    height: 10px;
    background: linear-gradient(90deg, var(--band-cyan), var(--band-violet) 40%, var(--band-red) 75%, var(--band-orange));
  }
  .brand-mark {
    display: flex;
    align-items: center;
    gap: 10px;
    color: var(--ink-light);
    font-family: "Questrial", "Century Gothic", sans-serif;
    letter-spacing: 0.14em;
    text-transform: uppercase;
    white-space: nowrap;
  }
  .brand-mark__dot {
    border-radius: 50%;
    background: var(--accent-cyan);
    flex: none;
  }
  /* Contact side */
  .deco-area {
    position: absolute;
    left: 0; bottom: 10px;
    width: 250px; height: 200px;
    background: var(--deco-grey);
    border-top-right-radius: 120px;
  }
  .contact-brand {
    position: absolute;
    right: 40px; top: 40px;
    font-size: 17px;
  }
  .contact-brand .brand-mark__dot { width: 22px; height: 22px; }
  .contact-info {
    position: absolute;
    right: 40px; top: 110px;
    width: 230px;
    text-align: right;
    color: var(--ink-light);
  }
  .contact-info__name {
    font-family: "Montserrat", sans-serif;
    font-weight: 700;
    font-size: 19px;
    letter-spacing: 0.03em;
    color: var(--accent-cyan);
    text-transform: uppercase;
    white-space: nowrap;
  }
  .contact-info__title { font-size: 14px; margin-top: 4px; }
  .contact-info__rule {
    height: 1px;
    background: var(--accent-cyan);
    margin: 12px 0 12px -40px;
  }
  .contact-info__line {
    display: flex; justify-content: flex-end; align-items: center;
    gap: 8px; font-size: 13px; margin-top: 6px; white-space: nowrap;
  }
  .icon { width: 12px; height: 12px; fill: var(--accent-cyan); flex: none; }
  /* Product side */
  .product-brand {
    position: absolute;
    left: 0; right: 0; top: 96px;
    justify-content: center;
    font-size: 34px;
  }
  .product-brand .brand-mark__dot { width: 42px; height: 42px; }
  .product-web {
    position: absolute; left: 0; right: 0; top: 200px;
    display: flex; justify-content: center; align-items: center; gap: 8px;
    color: var(--ink-light); font-size: 14px; letter-spacing: 0.05em;
  }
  .product-tagline {
    position: absolute; left: 0; right: 0; top: 232px;
    text-align: center; color: var(--ink-light); font-size: 16px; letter-spacing: 0.02em;
  }
</style>
</head>
<body>
  <section class="card card--contact">
    <div class="deco-area" role="img" aria-label="Large grey brand illustration in the corner"></div>
    <div class="brand-mark contact-brand"><span class="brand-mark__dot"></span>Brightloom Language</div>
    <div class="contact-info">
      <p class="contact-info__name">Perry Dunmore</p>
      <p class="contact-info__title">Founder &amp; CEO</p>
      <div class="contact-info__rule"></div>
      <p class="contact-info__line">(555)-014-2286
        <svg class="icon" viewBox="0 0 24 24"><path d="M6.6 10.8a15 15 0 0 0 6.6 6.6l2.2-2.2a1 1 0 0 1 1-.25 11.4 11.4 0 0 0 3.6.57 1 1 0 0 1 1 1V20a1 1 0 0 1-1 1A17 17 0 0 1 3 4a1 1 0 0 1 1-1h3.5a1 1 0 0 1 1 1c0 1.25.2 2.45.57 3.6a1 1 0 0 1-.25 1z"/></svg>
      </p>
      <p class="contact-info__line">pdunmore@quillpost-mail.net
        <svg class="icon" viewBox="0 0 24 24"><path d="M2 5h20v14H2z M4 7v.5l8 5 8-5V7l-8 5z" fill-rule="evenodd"/></svg>
      </p>
    </div>
    <div class="card__band"></div>
  </section>

  <section class="card card--product">
    <div class="brand-mark product-brand"><span class="brand-mark__dot"></span>Glimworld</div>
    <p class="product-web">
      <svg class="icon" viewBox="0 0 24 24"><circle cx="12" cy="12" r="10"/></svg>
      www.glimworld-play.com
    </p>
    <p class="product-tagline">Culturally Immersive Language Learning Games</p>
    <div class="card__band"></div>
  </section>
</body>
</html>
```